interior designer/stylist looking for a letter press business card to reflect the stylish work

Hello Designers,
I need a business card design for an company called Mosaic Interior Design. I'm aiming at the high end residential and private client market in London providing sleek simple interiors. I'd like my business card to be pinterest worthy and expensive looking, i want people to pin it and for it to have a sought after look, and want prospective customers to hire me as their interior designer as my card is so beautiful.
I love letter press design. I also like the use of colour/foil on the edge.
Colour combos & general things I like -
Black and White
Navy Blue and Gold
Neutral colours (muted palette of greys whites navys beiges)
White Marble & brass
Vorelle (fashion designer)
....also open to other suggestions....
Please dont take the pink in the attached photos too literally. i'd like the card to look more masculine than feminine.
I'd like Mosaic on one side in one font, with interior design underneath so one word will make the statement....... unless anyone has any other ideas, open to suggestions.
I'd like a really simple font and for the whole card to look very graphic.
my details -
Petra Wendlecombe
Interior Designer & Stylist
email petra@mosaicinteriordesign.co.uk
phone +447311584209
website wwww.mosaicinteriordesign.co.uk
GO GO GO!! EXCITED TO SEE THE OUTCOME!!
x P
Target Market(s)
High End Residential and private clients
Industry/Entity Type
Business
Contact Information for Business Card
Mosaic Interior Design & Styling
Petra Wendlecombe
phone +447311584209

```html
<!DOCTYPE html>
<html lang="en">
<head>
<meta charset="utf-8">
<title>Mosaic Interior Design – Business Card</title>
<link href="https://fonts.googleapis.com/css2?family=Share+Tech+Mono&display=swap" rel="stylesheet">
<style>
  :root {
    --gold-deep: #c9a23e;
    --gold-mid: #e2c069;
    --gold-light: #f3de98;
    --card-white: #ffffff;
    --ink: #3d3d3d;
  }
  html, body {
    margin: 0;
    padding: 0;
    width: 1200px;
    height: 686px;
    overflow: hidden;
    background: var(--card-white);
  }
  .card {
    position: relative;
    width: 1200px;
    height: 686px;
    background:
      linear-gradient(115deg, var(--gold-light) 0%, var(--gold-mid) 22%, var(--gold-deep) 45%, var(--gold-mid) 62%, var(--gold-light) 80%, var(--gold-deep) 100%);
    overflow: hidden;
  }
  .card-face {
    position: absolute;
    top: 11px;
    left: 11px;
    right: 12px;
    bottom: 13px;
    background: var(--card-white);
  }
  .wordmark {
    position: absolute;
    left: 0;
    right: 0;
    text-align: center;
    font-family: "Share Tech Mono", monospace;
    color: var(--ink);
    margin: 0;
    font-weight: 400;
  }
  .wordmark-name {
    top: 228px;
    font-size: 147px;
    line-height: 147px;
    letter-spacing: 11px;
    padding-left: 11px;
  }
  .wordmark-tagline {
    top: 380px;
    font-size: 52px;
    line-height: 52px;
    letter-spacing: 1px;
    padding-left: 1px;
  }
  .wordmark-tagline span {
    display: inline-block;
    transform: scale(0.88, 1.12);
  }
</style>
</head>
<body>
  <div class="card">
    <div class="card-face">
      <h1 class="wordmark wordmark-name">MOSAIC</h1>
      <p class="wordmark wordmark-tagline"><span>INTERIOR DESIGN</span></p>
    </div>
  </div>
</body>
</html>
```